SOLVE Study flyer

I need help designing a flyer for a research study that will include brain imaging in adolescents. The info is in the attached document. The study is called the Sequoia Outlook Lantern Valley Echo (SOLVE) study. Ideally this would be returned as a document that I can edit in the future as we will have several new recruitment phases (different age groups, etc. I also would love to have a logo designed as part of this project, but I recognize that might be a separate design request.

```html
<!DOCTYPE html>
<html lang="en">
<head>
<meta charset="utf-8">
<title>SOLVE Study Flyer</title>
<link href="https://fonts.googleapis.com/css2?family=Saira+Condensed:ital,wght@0,700;0,800;1,700&family=Outfit:wght@400;500&display=swap" rel="stylesheet">
<style>
  :root {
    --teal: #008272;
    --white: #ffffff;
    --ink: #1a1a1a;
    --page: #ffffff;
  }
  * { box-sizing: border-box; margin: 0; padding: 0; }
  html, body { width: 906px; height: 1200px; overflow: hidden; background: var(--page); }
  .flyer { position: relative; width: 906px; height: 1200px; background: var(--white); font-family: "Outfit", sans-serif; color: var(--ink); }
  .display { font-family: "Saira Condensed", sans-serif; font-weight: 800; text-transform: uppercase; }

  .masthead { position: absolute; left: 0; top: 0; width: 906px; height: 114px; background: var(--teal); display: flex; align-items: center; justify-content: center; }
  .masthead h1 { color: var(--white); font-size: 37px; line-height: 37px; text-align: center; letter-spacing: 0.5px; }

  .headline { position: absolute; left: 0; top: 132px; width: 906px; text-align: center; color: var(--teal); font-size: 60px; line-height: 52px; letter-spacing: 0.3px; }

  .intro { position: absolute; left: 90px; top: 300px; width: 726px; text-align: center; font-size: 19px; line-height: 27px; }

  .panel { position: absolute; left: 53px; width: 800px; border: 2px solid var(--teal); border-radius: 28px; }
  .panel-label { position: absolute; left: 50%; transform: translateX(-50%); top: -20px; height: 44px; background: var(--teal); color: var(--white); border-radius: 8px; display: flex; align-items: center; justify-content: center; font-size: 28px; letter-spacing: 0.5px; white-space: nowrap; }

  .involves { top: 422px; height: 302px; }
  .involves .panel-label { width: 488px; }
  .steps { list-style: none; position: absolute; left: 74px; top: 66px; width: 700px; font-size: 21px; line-height: 23px; }
  .steps li { position: relative; padding-left: 32px; margin-bottom: 24px; }
  .steps li::before { content: ""; position: absolute; left: 0; top: 5px; width: 12px; height: 12px; border-radius: 50%; background: var(--teal); }

  .eligible { top: 758px; height: 266px; }
  .eligible .panel-label { width: 596px; }
  .criteria { position: absolute; left: 0; top: 60px; width: 100%; }
  .criterion { position: absolute; text-align: center; font-size: 17px; line-height: 21px; font-weight: 500; }
  .criterion .badge { display: block; width: 116px; height: 116px; border-radius: 50%; background: var(--teal); margin: 0 auto 20px; }
  .c-age { left: 20px; width: 150px; }
  .c-worry { left: 215px; width: 260px; }
  .c-diag { left: 510px; width: 250px; }

  .footer { position: absolute; left: 0; top: 1044px; width: 906px; height: 156px; background: var(--teal); }
  .footer .cta { position: absolute; left: 0; top: 10px; width: 906px; text-align: center; color: var(--white); font-family: "Saira Condensed", sans-serif; font-style: italic; font-weight: 700; text-transform: uppercase; font-size: 30px; line-height: 31px; letter-spacing: 0.4px; }
  .contact { position: absolute; left: 86px; top: 104px; display: flex; align-items: center; gap: 14px; color: var(--white); font-size: 26px; }
  .contact svg { width: 40px; height: 40px; }
  .compensation { position: absolute; right: 0; top: 84px; width: 336px; height: 72px; background: var(--white); border-radius: 20px 0 0 0; display: flex; align-items: center; justify-content: center; text-align: center; color: var(--teal); font-size: 33px; line-height: 30px; }
</style>
</head>
<body>
<main class="flyer">
  <header class="masthead">
    <h1 class="display">Sequoia Outlook Lantern<br>Valley Echo</h1>
  </header>

  <h2 class="headline display">Are you the parent of a child<br>age 10-17? Do they worry or<br>overthink negative emotions?</h2>

  <p class="intro">Ridgeline University researchers are seeking girls age 10-17 for a study about brain activity in emotions and decision-making and how they relate to puberty, anxiety and depression.</p>

  <section class="panel involves">
    <div class="panel-label display">Study participation involves</div>
    <ul class="steps">
      <li>One one-hour interview (online or in-person) where your child will discuss their thoughts</li>
      <li>Online questionnaires (parent and child)</li>
      <li>One two-hour visit where your child will complete an MRI scan, answer questions about their puberty stage, and have a small hair sample taken to study puberty hormones</li>
    </ul>
  </section>

  <section class="panel eligible">
    <div class="panel-label display">Your child may be eligible if they</div>
    <div class="criteria">
      <div class="criterion c-age"><span class="badge" role="img" aria-label="Age icon"></span>Are age 10-17</div>
      <div class="criterion c-worry"><span class="badge" role="img" aria-label="Icon of a head with question marks"></span>Tend to worry or overthink<br>negative thoughts</div>
      <div class="criterion c-diag"><span class="badge" role="img" aria-label="Icon of a child with puzzle pieces"></span>Have not been diagnosed<br>with psychosis, learning<br>problems, or autism</div>
    </div>
  </section>

  <footer class="footer">
    <p class="cta">Interested in participating?<br>Want more information? Please contact us!</p>
    <div class="contact">
      <svg viewBox="0 0 40 40" aria-hidden="true">
        <circle cx="20" cy="20" r="20" fill="#ffffff"/>
        <rect x="11" y="14" width="18" height="12" fill="none" stroke="#008272" stroke-width="1.6"/>
        <polyline points="11,14 20,21 29,14" fill="none" stroke="#008272" stroke-width="1.6"/>
      </svg>
      <span>solvestudy@ridgeline.edu</span>
    </div>
    <div class="compensation display">Compensation<br>up to $140</div>
  </footer>
</main>
</body>
</html>
```